Industrial Project Sign

We need an eye catching (but professional) industrial project sign that will be very large (roughly 12' high x 18' wide). This sign will be highly visible from the adjacent high speed highway.

* The following needs to be at the bottom of the signage: Logo (uploaded), Name (Brightline Property Partners, Inc.) (uploaded) and phone number (415)736-2958

*Name of Project - "Meridale Commerce Park"

* Text items
Land for Sale
Build to Suit
Zoning: Industrial (G I & L I)

* Interesting background that is eye catching
Updates

Good morning all,

We are considering all designers options as we go and are waiting for the final designs to come in by the 4th so that we can give each one a good look.   If you have any new designs, questions, further design options or any tweeks you want to do to current designs, please do so at this time.

Thanks to all of you for your submissions.

Industry/Entity Type

Industrial

```html
<!DOCTYPE html>
<html lang="en">
<head>
<meta charset="utf-8">
<title>Brightline Property Partners – Meridale Commerce Park Sign</title>
<link rel="stylesheet" href="https://fonts.googleapis.com/css2?family=Oswald:wght@700&family=Arimo:wght@700&display=swap">
<style>
  :root {
    --maroon: #3a0000;
    --white: #ffffff;
    --page: #ffffff;
  }
  * { margin: 0; padding: 0; box-sizing: border-box; }
  html, body {
    width: 1200px;
    height: 999px;
    overflow: hidden;
    background: var(--page);
  }
  .canvas {
    position: relative;
    width: 1200px;
    height: 999px;
  }
  .sign {
    position: absolute;
    width: 810px;
    height: 541px;
    background: var(--maroon);
    overflow: hidden;
    transform-origin: 0 0;
  }
  .sign--large { left: 195px; top: 37px; }
  .sign--small { left: 845px; top: 745px; transform: scale(0.395); }

  .sign__header {
    position: absolute;
    left: 0; top: 0;
    width: 810px; height: 200px;
  }
  .sign__brand {
    position: absolute;
    left: 0; top: 62px;
    width: 810px;
    display: flex;
    align-items: center;
    justify-content: center;
    gap: 16px;
  }
  .brand__mark {
    width: 40px; height: 40px;
    background: var(--maroon);
  }
  .brand__text {
    display: flex;
    flex-direction: column;
    align-items: flex-start;
    gap: 4px;
  }
  .brand__name {
    font-family: "Arimo", Arial, sans-serif;
    font-weight: 700;
    font-size: 22px;
    line-height: 1;
    color: var(--maroon);
    white-space: nowrap;
    padding-bottom: 5px;
    border-bottom: 4px solid var(--maroon);
  }
  .brand__project {
    font-family: "Arimo", Arial, sans-serif;
    font-weight: 700;
    font-size: 16px;
    line-height: 1;
    color: var(--maroon);
    white-space: nowrap;
  }
  .sign__headline {
    position: absolute;
    left: 0;
    width: 810px;
    text-align: center;
    font-family: "Oswald", "Arial Narrow", sans-serif;
    font-weight: 700;
    font-size: 120px;
    line-height: 1;
    color: var(--white);
    white-space: nowrap;
    transform: scaleX(0.96);
  }
  .sign__headline--first { top: 172px; }
  .sign__headline--second { top: 285px; }
  .sign__zoning {
    position: absolute;
    left: 0; top: 404px;
    width: 810px;
    text-align: center;
    font-family: "Arimo", Arial, sans-serif;
    font-weight: 700;
    font-size: 40px;
    letter-spacing: 2.5px;
    line-height: 1;
    color: var(--white);
    white-space: nowrap;
  }
  .sign__contact {
    position: absolute;
    left: 3px; top: 454px;
    width: 804px; height: 79px;
    background: var(--white);
    display: flex;
    align-items: center;
    justify-content: center;
    font-family: "Oswald", "Arial Narrow", sans-serif;
    font-weight: 700;
    font-size: 64px;
    line-height: 1;
    color: var(--maroon);
    white-space: nowrap;
  }
</style>
</head>
<body>
<div class="canvas">

  <section class="sign sign--large" aria-label="Land for sale sign">
    <svg class="sign__header" viewBox="0 0 810 200" aria-hidden="true">
      <ellipse cx="405" cy="95" rx="440" ry="80" fill="var(--white)"/>
    </svg>
    <div class="sign__brand">
      <span class="brand__mark"></span>
      <span class="brand__text">
        <span class="brand__name">Brightline Property Partners, Inc.</span>
        <span class="brand__project">Meridale Commerce Park</span>
      </span>
    </div>
    <h1 class="sign__headline sign__headline--first">LAND FOR SALE</h1>
    <h2 class="sign__headline sign__headline--second">BUILD TO SUIT</h2>
    <p class="sign__zoning">ZONING: INDUSTRIAL (G I &amp; L I)</p>
    <p class="sign__contact">Phone :(415) 736-2958</p>
  </section>

  <section class="sign sign--small" aria-label="Land for sale sign, small preview">
    <svg class="sign__header" viewBox="0 0 810 200" aria-hidden="true">
      <ellipse cx="405" cy="95" rx="440" ry="80" fill="var(--white)"/>
    </svg>
    <div class="sign__brand">
      <span class="brand__mark"></span>
      <span class="brand__text">
        <span class="brand__name">Brightline Property Partners, Inc.</span>
        <span class="brand__project">Meridale Commerce Park</span>
      </span>
    </div>
    <p class="sign__headline sign__headline--first">LAND FOR SALE</p>
    <p class="sign__headline sign__headline--second">BUILD TO SUIT</p>
    <p class="sign__zoning">ZONING: INDUSTRIAL (G I &amp; L I)</p>
    <p class="sign__contact">Phone :(415) 736-2958</p>
  </section>

</div>
</body>
</html>
```